Nivel Crest - Powerpoint Templates

We are a consultancy to help builders to optimize their planning in order to save building costs. For that reason we need templates for teasers and presentations where we offer our services, show our team and their capacities and present workflows, organization charts, price lists etc.

```html
<!DOCTYPE html>
<html lang="en">
<head>
<meta charset="utf-8">
<title>Nivel Crest – Presentation Templates</title>
<link href="https://fonts.googleapis.com/css2?family=Montserrat:wght@400;500;600;700&family=Oswald:wght@600;700&display=swap" rel="stylesheet">
<style>
:root{
  --bg:#d3d3d3;
  --paper:#ffffff;
  --ink:#1d1d1f;
  --text:#3a3a3a;
  --gold:#c8922f;
  --gold-light:#ecc466;
  --gold-deep:#a8741d;
  --slate:#3a3b42;
  --slate-light:#55565d;
  --table-head:#a9a9ab;
  --rule:#d9d9d9;
}
*{box-sizing:border-box;margin:0;padding:0}
html,body{width:750px;height:1200px;overflow:hidden;background:var(--bg)}
body{position:relative;font-family:"Montserrat",sans-serif;color:var(--text)}
.slide{position:absolute;width:295px;height:184px;background:var(--paper);overflow:hidden;box-shadow:0 9px 7px -5px rgba(0,0,0,.35)}
.col-a{left:60px}.col-b{left:395px}
.row-1{top:62px}.row-2{top:280px}.row-3{top:497px}.row-4{top:715px}.row-5{top:938px}
.abs{position:absolute}
.heading{position:absolute;left:11px;top:9px;font-size:9px;font-weight:400;color:var(--ink);white-space:nowrap}
.heading span{color:var(--gold)}
.brand{position:absolute;right:10px;top:12px;display:flex;align-items:center;gap:2px;font-size:4.6px;font-weight:700;color:var(--gold);letter-spacing:.3px}
.brand i{display:block;width:5px;height:5px;background:var(--gold)}
.brand.on-dark{color:#fff}.brand.on-dark i{background:#fff}
.footer-rule{position:absolute;left:0;bottom:8px;width:250px;height:2px;background:linear-gradient(90deg,var(--gold-deep),var(--gold-light) 70%,var(--gold))}
.footer-tag{position:absolute;right:10px;bottom:6px;font-size:3.2px;font-weight:500;color:var(--ink)}
.footer-tag span{color:var(--gold)}
.footer-tag.on-dark{color:#fff}
.copy{font-size:3.1px;line-height:1.32;text-align:justify;color:var(--text)}
.copy + .copy{margin-top:3px}
.service-title{font-size:6px;color:var(--gold);margin:6px 0 3px}
.sub-gold{font-size:6.2px;font-weight:600;color:var(--gold-deep)}
.bullets{list-style:none}
.bullets li{position:relative;padding-left:5px;font-size:3.1px;line-height:1.3;text-align:justify;margin-top:8px}
.bullets li::before{content:"";position:absolute;left:0;top:1px;width:1.6px;height:1.6px;background:currentColor}
.photo{position:absolute}
.big-title{font-family:"Oswald",sans-serif;font-weight:700;line-height:1;letter-spacing:-.2px;white-space:nowrap}
.brand-lg{position:absolute;left:13px;top:20px;display:flex;align-items:center;gap:4px;font-size:11px;font-weight:700;color:var(--gold);letter-spacing:.5px}
.brand-lg i{display:block;width:12px;height:12px;background:var(--gold)}
.frame{position:absolute;top:37px;width:61px;height:55px;border:2.5px solid var(--gold);background:linear-gradient(160deg,#8aa3c4,#d7dbe2 45%,#c89a86 80%,#e6c7b8)}
.card-title{position:absolute;top:99px;width:69px;text-align:center;font-size:5.5px;font-weight:500;color:var(--ink)}
.card-copy{position:absolute;top:107px;width:61px;text-align:center;font-size:3px;line-height:1.25}
.icon-dot{position:absolute;width:20px;height:20px;border-radius:50%;display:flex;align-items:center;justify-content:center}
.icon-dot.dark{background:radial-gradient(circle at 40% 35%,#5a5b62,#26272c)}
.icon-dot.gold{background:radial-gradient(circle at 40% 35%,var(--gold-light),var(--gold-deep))}
.item-title{font-size:5.5px;font-weight:500;color:var(--ink)}
.item-copy{font-size:3.1px;line-height:1.25;margin-top:1px}
.data{position:absolute;left:11px;top:42px;width:273px;border-collapse:collapse;font-size:3.6px;color:var(--ink)}
.data th{background:var(--table-head);color:#fff;font-weight:400;height:14px;font-size:3.4px;line-height:1.1}
.data th:first-child{text-align:left;padding-left:2px}
.data td{height:12.3px;text-align:center;border-bottom:.6px solid var(--rule)}
.data td:first-child{text-align:left;padding-left:2px;width:84px}
.data th.hl{background:var(--gold)}
.col-outline{position:absolute;left:95px;top:38px;width:47px;height:108px;border:.8px solid var(--gold);border-radius:4px}
.panel{position:absolute;top:49px;width:63px;height:100px;background:linear-gradient(180deg,var(--gold-deep),var(--gold) 40%,var(--gold-light));border-bottom:3px solid #111;text-align:center;color:#fff}
.panel .icon-dot{position:static;margin:6px auto 0;width:11px;height:11px;background:#1d1d1f}
.panel h4{font-size:7px;font-weight:400;margin-top:4px}
.panel p{font-size:3.2px;line-height:1.3;padding:2px 8px 0;color:#fbe9c5}
</style>
</head>
<body>

<!-- 1 · Cover -->
<section class="slide col-a row-1">
  <svg class="abs" width="295" height="184" viewBox="0 0 295 184">
    <defs>
      <linearGradient id="cityWarm" x1="0" y1="0" x2="0" y2="1">
        <stop offset="0" stop-color="#b8a46a"/><stop offset=".5" stop-color="#8c7a4c"/><stop offset="1" stop-color="#3f3a2c"/>
      </linearGradient>
      <linearGradient id="towerPhoto" x1="0" y1="0" x2="0" y2="1">
        <stop offset="0" stop-color="#4aa3e0"/><stop offset=".55" stop-color="#9cc6e6"/><stop offset=".7" stop-color="#5c8a55"/><stop offset="1" stop-color="#5e8aa0"/>
      </linearGradient>
    </defs>
    <polygon points="198,0 206,0 171,184 163,184" fill="var(--gold)"/>
    <polygon role="img" aria-label="Hazy golden city skyline photograph" points="206,0 295,0 295,184 171,184" fill="url(#cityWarm)"/>
    <circle cx="180" cy="88" r="46" fill="#2f3035"/>
    <circle role="img" aria-label="Photo of modern towers beside a river" cx="180" cy="88" r="42" fill="url(#towerPhoto)"/>
  </svg>
  <div class="brand-lg"><i></i>NIVEL CREST</div>
  <div class="abs big-title" style="left:13px;top:117px;font-size:19.5px;color:var(--ink)">PRESENTATION</div>
  <div class="abs big-title" style="left:13px;top:138px;font-size:19.5px;color:var(--gold)">TITLE GOESHERE</div>
  <div class="abs" style="left:13px;top:165px;font-size:6px;color:var(--ink)">Subtitle of Presentation Goes Here</div>
</section>

<!-- 2 · Services text -->
<section class="slide col-b row-1">
  <h2 class="heading"><span>Heading</span> Goes Here</h2>
  <div class="brand"><i></i>NIVEL CREST</div>
  <div class="abs" style="left:11px;top:27px;width:273px">
    <h3 class="service-title">Service Title Goes Here</h3>
    <p class="copy">Lorem ipsum dolor sit amet, consectetuer adipiscing elit, sed diam nonummy nibh euismod tincidunt ut laoreet dolore magna aliquam erat volutpat. Ut wisi enim ad minim veniam, quis nostrud exerci tation ullamcorper suscipit lobortis nisl ut aliquip ex ea commodo consequat. Duis autem vel eum iriure dolor in hendrerit in vulputate velit esse molestie consequat, vel illum dolore eu feugiat nulla facilisis at vero eros et accumsan et iusto odio dignissim.</p>
    <p class="copy">Lorem ipsum dolor sit amet, consectetuer adipiscing elit, sed diam nonummy nibh euismod tincidunt ut laoreet dolore magna aliquam erat volutpat. Ut wisi enim ad minim veniam, quis nostrud exerci tation ullamcorper suscipit lobortis nisl ut aliquip ex ea commodo consequat. Duis autem vel eum iriure dolor in hendrerit in vulputate velit esse molestie consequat, vel illum dolore eu feugiat nulla facilisis at vero eros et accumsan et iusto odio dignissim qui blandit praesent luptatum zzril. Lorem ipsum dolor sit amet, consectetuer adipiscing elit, sed diam nonummy nibh euismod tincidunt ut laoreet dolore magna aliquam erat volutpat.</p>
    <h3 class="service-title">Service Title Goes Here</h3>
    <p class="copy">Lorem ipsum dolor sit amet, consectetuer adipiscing elit, sed diam nonummy nibh euismod tincidunt ut laoreet dolore magna aliquam erat volutpat. Ut wisi enim ad minim veniam, quis nostrud exerci tation ullamcorper suscipit lobortis nisl ut aliquip ex ea commodo consequat. Duis autem vel eum iriure dolor in hendrerit in vulputate velit esse molestie consequat, vel illum dolore eu feugiat nulla facilisis at vero eros et accumsan et iusto odio dignissim qui blandit praesent luptatum zzril. Lorem ipsum dolor sit amet, consectetuer adipiscing elit, sed diam nonummy nibh euismod tincidunt ut laoreet dolore magna aliquam erat volutpat. Duis autem vel eum iriure dolor in hendrerit in vulputate praes.</p>
  </div>
  <div class="footer-rule"></div><div class="footer-tag">NIVEL CREST <span>| 01</span></div>
</section>

<!-- 3 · Four cards -->
<section class="slide col-a row-2">
  <h2 class="heading"><span>Heading</span> Goes Here</h2>
  <div class="brand"><i></i>NIVEL CREST</div>
  <div class="frame" role="img" aria-label="Photo of colleagues reviewing a tablet at a desk" style="left:15px"></div>
  <div class="frame" role="img" aria-label="Photo of colleagues reviewing a tablet at a desk" style="left:84px"></div>
  <div class="frame" role="img" aria-label="Photo of colleagues reviewing a tablet at a desk" style="left:153px"></div>
  <div class="frame" role="img" aria-label="Photo of colleagues reviewing a tablet at a desk" style="left:222px"></div>
  <div class="card-title" style="left:11px">Title Goes Here</div>
  <div class="card-title" style="left:80px">Title Goes Here</div>
  <div class="card-title" style="left:149px">Title Goes Here</div>
  <div class="card-title" style="left:218px">Title Goes Here</div>
  <p class="card-copy" style="left:15px">Lorem ipsum dolor sit amet, consectetuer adipiscing elit, sed diam nonummy nibh euismod tincidunt ut laoreet dolore magna aliquam erat volutpat. Ut wisi enim ad minim veniam, quis nostrud exerci tation ullamcorper suscipit lobortis nisl ut aliquip ex ea commodo consequat. Duis autem vel eum iriure dolor in hendrerit in vulputate velit esse molestie consequat.</p>
  <p class="card-copy" style="left:84px">Lorem ipsum dolor sit amet, consectetuer adipiscing elit, sed diam nonummy nibh euismod tincidunt ut laoreet dolore magna aliquam erat volutpat. Ut wisi enim ad minim veniam, quis nostrud exerci tation ullamcorper suscipit lobortis nisl ut aliquip ex ea commodo consequat. Duis autem vel eum iriure dolor in hendrerit in vulputate velit esse molestie consequat.</p>
  <p class="card-copy" style="left:153px">Lorem ipsum dolor sit amet, consectetuer adipiscing elit, sed diam nonummy nibh euismod tincidunt ut laoreet dolore magna aliquam erat volutpat. Ut wisi enim ad minim veniam, quis nostrud exerci tation ullamcorper suscipit lobortis nisl ut aliquip ex ea commodo consequat. Duis autem vel eum iriure dolor in hendrerit in vulputate velit esse molestie consequat.</p>
  <p class="card-copy" style="left:222px">Lorem ipsum dolor sit amet, consectetuer adipiscing elit, sed diam nonummy nibh euismod tincidunt ut laoreet dolore magna aliquam erat volutpat. Ut wisi enim ad minim veniam, quis nostrud exerci tation ullamcorper suscipit lobortis nisl ut aliquip ex ea commodo consequat. Duis autem vel eum iriure dolor in hendrerit in vulputate velit esse molestie consequat.</p>
  <div class="footer-rule"></div><div class="footer-tag">NIVEL CREST <span>| 01</span></div>
</section>

<!-- 4 · Icon list with dark city -->
<section class="slide col-b row-2">
  <svg class="abs" width="295" height="184" viewBox="0 0 295 184">
    <defs>
      <linearGradient id="cityDark" x1="0" y1="0" x2="0" y2="1">
        <stop offset="0" stop-color="#3b3d46"/><stop offset=".45" stop-color="#6f727b"/><stop offset="1" stop-color="#22242a"/>
      </linearGradient>
    </defs>
    <polygon role="img" aria-label="Dark misty city skyline photograph" points="197,0 295,0 295,184 150,184" fill="url(#cityDark)"/>
  </svg>
  <h2 class="heading"><span>Heading</span> Goes Here</h2>
  <div class="brand on-dark"><i></i>NIVEL CREST</div>
  <div class="icon-dot dark" style="left:11px;top:52px"><svg width="9" height="9" viewBox="0 0 10 10"><rect x="1" y="3" width="8" height="6" rx="1" fill="#fff"/><rect x="3.5" y="1" width="3" height="2.5" fill="none" stroke="#fff"/></svg></div>
  <div class="icon-dot gold" style="left:11px;top:88px"><svg width="9" height="9" viewBox="0 0 10 10"><rect x="1" y="3" width="8" height="6" rx="1" fill="#fff"/><rect x="3.5" y="1" width="3" height="2.5" fill="none" stroke="#fff"/></svg></div>
  <div class="icon-dot dark" style="left:11px;top:125px"><svg width="9" height="9" viewBox="0 0 10 10"><rect x="1" y="3" width="8" height="6" rx="1" fill="#fff"/><rect x="3.5" y="1" width="3" height="2.5" fill="none" stroke="#fff"/></svg></div>
  <div class="abs" style="left:41px;top:50px;width:102px"><div class="item-title">Title Goes Here</div><p class="item-copy">Lorem ipsum dolor sit amet, consectetuer adipiscing elit, sed diam nonummy nibh euismod tincidunt ut laoreet dolore magna aliquam erat volutpat. Ut wisi enim ad minim veniam, quis nostrud exerci tation ullamcorper suscipit lobortis nisl ut</p></div>
  <div class="abs" style="left:41px;top:86px;width:102px"><div class="item-title">Title Goes Here</div><p class="item-copy">Lorem ipsum dolor sit amet, consectetuer adipiscing elit, sed diam nonummy nibh euismod tincidunt ut laoreet dolore magna aliquam erat volutpat. Ut wisi enim ad minim veniam, quis nostrud exerci tation ullamcorper suscipit lobortis nisl ut</p></div>
  <div class="abs" style="left:41px;top:123px;width:102px"><div class="item-title">Title Goes Here</div><p class="item-copy">Lorem ipsum dolor sit amet, consectetuer adipiscing elit, sed diam nonummy nibh euismod tincidunt ut laoreet dolore magna aliquam erat volutpat. Ut wisi enim ad minim veniam, quis nostrud exerci tation ullamcorper suscipit lobortis nisl ut</p></div>
  <div class="footer-tag on-dark">NIVEL CREST &nbsp;01</div>
</section>

<!-- 5 · Split comparison -->
<section class="slide col-a row-3">
  <div class="abs" style="left:148px;top:0;width:147px;height:184px;background:linear-gradient(170deg,var(--slate),var(--slate-light))"></div>
  <h2 class="heading"><span>Heading</span> Goes Here</h2>
  <div class="brand on-dark"><i></i>NIVEL CREST</div>
  <div class="abs" style="left:12px;top:39px;width:131px">
    <h3 class="sub-gold">Curabitur Dapibus Dignissim Dui.</h3>
    <ul class="bullets" style="color:var(--ink)">
      <li>Lorem ipsum dolor sit amet, consectetuer adipiscing elit, sed diam nonummy nibh euismod tincidunt ut laoreet dolore magna aliquam erat volutpat. Ut wisi enim ad minim veniam,</li>
      <li style="margin-top:10px">Lorem ipsum dolor sit amet, consectetuer adipiscing elit, sed diam nonummy nibh euismod tincidunt ut laoreet dolore magna aliquam erat volutpat. Ut wisi enim ad minim veniam, quis nostrud exerci tation ullamcorper suscipit lobortis nisl ut aliquip ex ea commodo consequat. Duis autem vel eum iriure dolor in hendrerit in vulputate velit esse molestie consequat,</li>
      <li style="margin-top:10px">Lorem ipsum dolor sit amet, consectetuer adipiscing elit, sed diam nonummy nibh euismod tincidunt ut laoreet dolore magna aliquam erat volutpat. Ut wisi enim ad minim veniam, quis nostrud exerci tation ullamcorper suscipit lobortis nisl ut aliquip ex ea commodo consequat. Duis autem vel eum iriure dolor in hendrerit in vulputate velit esse molestie consequat,</li>
    </ul>
  </div>
  <div class="abs" style="left:155px;top:39px;width:131px;color:#fff">
    <h3 class="sub-gold" style="color:#fff;font-weight:500">Curabitur Dapibus Dignissim Dui.</h3>
    <ul class="bullets" style="color:#eee">
      <li>Lorem ipsum dolor sit amet, consectetuer adipiscing elit, sed diam nonummy nibh euismod tincidunt ut laoreet dolore magna aliquam erat volutpat. Ut wisi enim ad minim veniam,</li>
      <li style="margin-top:10px">Lorem ipsum dolor sit amet, consectetuer adipiscing elit, sed diam nonummy nibh euismod tincidunt ut laoreet dolore magna aliquam erat volutpat. Ut wisi enim ad minim veniam, quis nostrud exerci tation ullamcorper suscipit lobortis nisl ut aliquip ex ea commodo consequat. Duis autem vel eum iriure dolor in hendrerit in vulputate velit esse molestie consequat,</li>
      <li style="margin-top:10px">Lorem ipsum dolor sit amet, consectetuer adipiscing elit, sed diam nonummy nibh euismod tincidunt ut laoreet dolore magna aliquam erat volutpat. Ut wisi enim ad minim veniam, quis nostrud exerci tation ullamcorper suscipit lobortis nisl ut aliquip ex ea commodo consequat. Duis autem vel eum iriure dolor in hendrerit in vulputate velit esse molestie consequat,</li>
    </ul>
  </div>
  <div class="footer-tag on-dark">NIVEL CREST &nbsp;01</div>
</section>

<!-- 6 · Table -->
<section class="slide col-b row-3">
  <h2 class="heading"><span>Heading</span> Goes Here</h2>
  <div class="brand"><i></i>NIVEL CREST</div>
  <table class="data">
    <thead><tr><th>Heading Goes Here</th><th class="hl">Heading<br>Goes Here</th><th>Heading<br>Goes Here</th><th>Heading<br>Goes Here</th><th>Heading<br>Goes Here</th></tr></thead>
    <tbody>
      <tr><td>Lorem Ipsum Goes Here</td><td>23</td><td>12</td><td>78</td><td>12</td></tr>
      <tr><td>Lorem Ipsum Goes Here</td><td>45</td><td>56</td><td>12</td><td>56</td></tr>
      <tr><td>Lorem Ipsum Goes Here</td><td>78</td><td>76</td><td>34</td><td>76</td></tr>
      <tr><td>Lorem Ipsum Goes Here</td><td>22</td><td>12</td><td>55</td><td>12</td></tr>
      <tr><td>Lorem Ipsum Goes Here</td><td>34</td><td>66</td><td>45</td><td>66</td></tr>
      <tr><td>Lorem Ipsum Goes Here</td><td>67</td><td>47</td><td>78</td><td>47</td></tr>
      <tr><td>Lorem Ipsum Goes Here</td><td>87</td><td>67</td><td>12</td><td>67</td></tr>
    </tbody>
  </table>
  <div class="col-outline"></div>
  <div class="footer-rule"></div><div class="footer-tag">NIVEL CREST <span>| 01</span></div>
</section>

<!-- 7 · Company profile -->
<section class="slide col-a row-4">
  <h2 class="heading"><span>Heading</span> Goes Here</h2>
  <div class="brand"><i></i>NIVEL CREST</div>
  <div class="abs" style="left:9px;top:45px;width:277px">
    <p class="copy" style="font-size:3.4px;color:var(--ink)">Quillmar Resources Ltd is an exploration company with brownfield metals projects in North America. The company's strategy is to develop a portfolio of projects that support the green economy through the discovery and delivery of commodities that promote electrification and decarbonisation. We seek to maximise shareholder value through the acquisition, discovery and advancement of high quality precious, base and strategic metal projects in North America.</p>
    <p class="copy" style="font-size:3.4px;color:var(--ink);margin-top:4px">The company utilises the expertise of its exploration team to identify underexplored and undervalued high-grade metal projects with significant geological potential. The company has full ownership of the Tallowmere Copper Project and the Brackenvale Gold Project. Both assets are located in the same state.</p>
  </div>
  <div class="photo" role="img" aria-label="Photo of a team meeting in an office" style="left:13px;top:91px;width:80px;height:39px;background:linear-gradient(180deg,#cfd2d6,#7b7f86 60%,#3c3e44)"></div>
  <div class="photo" role="img" aria-label="Photo of a hand holding a glowing tablet" style="left:107px;top:91px;width:80px;height:39px;background:linear-gradient(160deg,#d9ecf7,#6aa4cf 55%,#1f3c63)"></div>
  <div class="photo" role="img" aria-label="Photo of colleagues reviewing a tablet at a desk" style="left:202px;top:91px;width:80px;height:39px;background:linear-gradient(160deg,#9fb4cf,#dfe2e8 50%,#c7a391)"></div>
  <div class="abs" style="left:13px;top:135px;width:80px;text-align:center;font-size:5.5px;color:var(--gold)">Heading Goes Here</div>
  <div class="abs" style="left:107px;top:135px;width:80px;text-align:center;font-size:5.5px;color:var(--gold)">Heading Goes Here</div>
  <div class="abs" style="left:202px;top:135px;width:80px;text-align:center;font-size:5.5px;color:var(--gold)">Heading Goes Here</div>
  <ul class="bullets abs" style="left:15px;top:142px;width:66px;color:var(--gold)"><li style="color:var(--ink);text-align:left;font-size:3.4px">Lorem ipsum dolar sit amet, consectetur adipising edit. Vivamus eu dui ex.</li></ul>
  <ul class="bullets abs" style="left:109px;top:142px;width:66px;color:var(--gold)"><li style="color:var(--ink);text-align:left;font-size:3.4px">Lorem ipsum dolar sit amet, consectetur adipising edit. Vivamus eu dui ex.</li></ul>
  <ul class="bullets abs" style="left:204px;top:142px;width:66px;color:var(--gold)"><li style="color:var(--ink);text-align:left;font-size:3.4px">Lorem ipsum dolar sit amet, consectetur adipising edit. Vivamus eu dui ex.</li></ul>
  <div class="footer-rule"></div><div class="footer-tag">NIVEL CREST <span>| 01</span></div>
</section>

<!-- 8 · Gold panels -->
<section class="slide col-b row-4">
  <h2 class="heading"><span>Heading</span> Goes Here</h2>
  <div class="brand"><i></i>NIVEL CREST</div>
  <div class="panel" style="left:15px"><div class="icon-dot"><svg width="6" height="6" viewBox="0 0 10 10"><rect x="1" y="3" width="8" height="6" rx="1" fill="#fff"/><rect x="3.5" y="1" width="3" height="2.5" fill="none" stroke="#fff"/></svg></div><h4>Heading</h4><p>Lorem ipsum dolor sit amet, consectetuer adipiscing elit, sed diam nonummy nibh euismod tincidunt ut laoreet dolore magna aliquam erat volutpat. Ut wisi enim ad minim veniam, quis nostrud exerci tation</p></div>
  <div class="panel" style="left:85px"><div class="icon-dot"><svg width="6" height="6" viewBox="0 0 10 10"><rect x="1" y="3" width="8" height="6" rx="1" fill="#fff"/><rect x="3.5" y="1" width="3" height="2.5" fill="none" stroke="#fff"/></svg></div><h4>Heading</h4><p>Lorem ipsum dolor sit amet, consectetuer adipiscing elit, sed diam nonummy nibh euismod tincidunt ut laoreet dolore magna aliquam erat volutpat. Ut wisi enim ad minim veniam, quis nostrud exerci tation</p></div>
  <div class="abs" style="left:158px;top:50px;width:126px">
    <h3 class="sub-gold">Curabitur Dapibus Dignissim Dui.</h3>
    <ul class="bullets" style="color:var(--ink)">
      <li>Lorem ipsum dolor sit amet, consectetuer adipiscing elit, sed diam nonummy nibh euismod tincidunt ut laoreet dolore magna aliquam erat volutpat. Ut wisi enim ad minim veniam,</li>
      <li style="margin-top:9px">Lorem ipsum dolor sit amet, consectetuer adipiscing elit, sed diam nonummy nibh euismod tincidunt ut laoreet dolore magna aliquam erat volutpat. Ut wisi enim ad minim veniam, quis nostrud exerci tation ullamcorper suscipit lobortis nisl ut aliquip ex ea commodo consequat. Duis autem vel eum iriure dolor in hendrerit in vulputate velit esse molestie consequat,</li>
      <li style="margin-top:9px">Lorem ipsum dolor sit amet, consectetuer adipiscing elit, sed diam nonummy nibh euismod tincidunt ut laoreet dolore magna aliquam erat volutpat. Ut wisi enim ad minim veniam, quis nostrud exerci tation ullamcorper suscipit lobortis nisl ut aliquip ex ea commodo consequat. Duis autem vel eum iriure dolor in hendrerit in vulputate velit esse molestie consequat,</li>
    </ul>
  </div>
  <div class="footer-rule"></div><div class="footer-tag">NIVEL CREST <span>| 01</span></div>
</section>

<!-- 9 · Six features -->
<section class="slide col-a row-5">
  <h2 class="heading"><span>Heading</span> Goes Here</h2>
  <div class="brand"><i></i>NIVEL CREST</div>
  <svg class="abs" width="295" height="184" viewBox="0 0 295 184">
    <g stroke="#cfcfcf" stroke-width=".6"><line x1="35" y1="43" x2="35" y2="67"/><line x1="35" y1="79" x2="35" y2="103"/><line x1="35" y1="116" x2="35" y2="140"/><line x1="176" y1="43" x2="176" y2="67"/><line x1="176" y1="79" x2="176" y2="103"/><line x1="176" y1="116" x2="176" y2="140"/></g>
  </svg>
  <div class="icon-dot gold" style="left:12px;top:45px"><svg width="9" height="9" viewBox="0 0 10 10"><rect x="1" y="3" width="8" height="6" rx="1" fill="#fff"/><rect x="3.5" y="1" width="3" height="2.5" fill="none" stroke="#fff"/></svg></div>
  <div class="icon-dot gold" style="left:12px;top:81px"><svg width="9" height="9" viewBox="0 0 10 10"><rect x="1" y="3" width="8" height="6" rx="1" fill="#fff"/><rect x="3.5" y="1" width="3" height="2.5" fill="none" stroke="#fff"/></svg></div>
  <div class="icon-dot gold" style="left:12px;top:118px"><svg width="9" height="9" viewBox="0 0 10 10"><rect x="1" y="3" width="8" height="6" rx="1" fill="#fff"/><rect x="3.5" y="1" width="3" height="2.5" fill="none" stroke="#fff"/></svg></div>
  <div class="icon-dot gold" style="left:153px;top:45px"><svg width="9" height="9" viewBox="0 0 10 10"><rect x="1" y="3" width="8" height="6" rx="1" fill="#fff"/><rect x="3.5" y="1" width="3" height="2.5" fill="none" stroke="#fff"/></svg></div>
  <div class="icon-dot gold" style="left:153px;top:81px"><svg width="9" height="9" viewBox="0 0 10 10"><rect x="1" y="3" width="8" height="6" rx="1" fill="#fff"/><rect x="3.5" y="1" width="3" height="2.5" fill="none" stroke="#fff"/></svg></div>
  <div class="icon-dot gold" style="left:153px;top:118px"><svg width="9" height="9" viewBox="0 0 10 10"><rect x="1" y="3" width="8" height="6" rx="1" fill="#fff"/><rect x="3.5" y="1" width="3" height="2.5" fill="none" stroke="#fff"/></svg></div>
  <div class="abs" style="left:42px;top:43px;width:98px"><div class="item-title">Title Goes Here</div><p class="item-copy" style="font-size:3.9px;color:var(--ink)">Lorem ipsum dolor sit amet, consectetuer adipiscing elit, sed diam nonummy nibh euismod tincidunt ut laoreet dolore magna</p></div>
  <div class="abs" style="left:42px;top:79px;width:98px"><div class="item-title">Title Goes Here</div><p class="item-copy" style="font-size:3.9px;color:var(--ink)">Lorem ipsum dolor sit amet, consectetuer adipiscing elit, sed diam nonummy nibh euismod tincidunt ut laoreet dolore magna</p></div>
  <div class="abs" style="left:42px;top:116px;width:98px"><div class="item-title">Title Goes Here</div><p class="item-copy" style="font-size:3.9px;color:var(--ink)">Lorem ipsum dolor sit amet, consectetuer adipiscing elit, sed diam nonummy nibh euismod tincidunt ut laoreet dolore magna</p></div>
  <div class="abs" style="left:183px;top:43px;width:98px"><div class="item-title">Title Goes Here</div><p class="item-copy" style="font-size:3.9px;color:var(--ink)">Lorem ipsum dolor sit amet, consectetuer adipiscing elit, sed diam nonummy nibh euismod tincidunt ut laoreet dolore magna</p></div>
  <div class="abs" style="left:183px;top:79px;width:98px"><div class="item-title">Title Goes Here</div><p class="item-copy" style="font-size:3.9px;color:var(--ink)">Lorem ipsum dolor sit amet, consectetuer adipiscing elit, sed diam nonummy nibh euismod tincidunt ut laoreet dolore magna</p></div>
  <div class="abs" style="left:183px;top:116px;width:98px"><div class="item-title">Title Goes Here</div><p class="item-copy" style="font-size:3.9px;color:var(--ink)">Lorem ipsum dolor sit amet, consectetuer adipiscing elit, sed diam nonummy nibh euismod tincidunt ut laoreet dolore magna</p></div>
  <div class="footer-rule"></div><div class="footer-tag">NIVEL CREST <span>| 01</span></div>
</section>

<!-- 10 · Closing -->
<section class="slide col-b row-5">
  <svg class="abs" width="295" height="184" viewBox="0 0 295 184">
    <defs>
      <linearGradient id="cityWarmEnd" x1="0" y1="0" x2="0" y2="1">
        <stop offset="0" stop-color="#c4ad6c"/><stop offset=".5" stop-color="#8c7a4c"/><stop offset="1" stop-color="#3f3a2c"/>
      </linearGradient>
    </defs>
    <polygon points="198,0 206,0 160,184 150,184" fill="var(--gold)"/>
    <polygon role="img" aria-label="Hazy golden city skyline photograph" points="206,0 295,0 295,184 160,184" fill="url(#cityWarmEnd)"/>
  </svg>
  <div class="brand-lg" style="top:22px"><i></i>NIVEL CREST</div>
  <div class="abs big-title" style="left:13px;top:67px;font-size:30px;color:var(--gold)">THANKS</div>
  <div class="abs big-title" style="left:13px;top:98px;font-size:30px;color:var(--ink)">YOU!</div>
  <div class="abs" style="left:13px;top:162px;font-size:4.8px;font-weight:500;color:var(--ink);line-height:1.6">
    <div><span style="color:var(--gold)">&#9737;</span> www.nivelcrest.com</div>
    <div><span style="color:var(--gold)">&#9993;</span> info@nivelcrest.com</div>
  </div>
  <div class="abs big-title" style="right:12px;top:128px;font-size:15.5px;color:#fff;text-align:right;line-height:1.05">PRESENTATION<br>TITLE GOESHERE</div>
  <div class="abs" style="right:12px;top:164px;font-size:5px;color:#fff">Subtitle of Presentation Goes Here</div>
</section>

</body>
</html>
```